Design a calming beauty medical salon & spa website based in Hong Kong

We need help building an informational website for a beauty salon in Hong Kong. The local salon provides facials, massages, body and other slimming treatments in a relaxing environment. We offer some non-invasive medical treatments, such as botox. Having built the business on word of mouth, it is now time for us to launch a website to help market the business better. Website requirements:

-Must be responsive
-Use vibrant but clean colours. not too many, 1-2 colours
-Must be bilingual (switch between Chinese traditional and English)
-Our current website is host on a server, not using any particular platforms like wordpress

Pages:
1/ Homepage
2/ About us (incorporate gallery of salon photos and history of company)
3/ Promotions and latest deals (and leads them to sign up for more info, maybe pop-up small window when you click on a promotion)
4/ Treatment menus
4.1/Body treatments
4.2/ Face treatments
4.3/ Slimming treatments
5/ Showcasing products sold (no e-commerce functionality, just showing off products)
6/ Contact us (tel, address, map, opening hrs)

Footer - must haves include contact us info, privacy policy, terms & conditions, copyright blurb, join our company/employment page (with a form)

For information (comparable websites we like):
http://veltora.com/
http://pambrix.com.hk/tc/aboutpambrix/background.php#centerenvi
Attaching a very first draft concept for this website
Attaching pictures of the beauty salon
Attaching logo

Target Market(s)

Hong Kong based, Chinese, females, 30-50+ age. 90% female clients.

Industry/Entity Type

Beauty Salon

Number of Pages Required

5+ page

Font styles to use
Sans Serif

Colors
f9d9e8
fbd3d4
fee3d5
fbe7d2
fee18a
fbf289
ffffff

Requirements
Must have
• interactive elements on website, such as scrolling banner photo headers
• incorporate photos of website salon
• connect to facebook page

```html
<!DOCTYPE html>
<html lang="en">
<head>
<meta charset="utf-8">
<title>Lumera Beauty</title>
<link href="https://fonts.googleapis.com/css2?family=Poppins:wght@400;500;600;700&family=Open+Sans:wght@400;600;700&display=swap" rel="stylesheet">
<style>
:root{
  --purple:#6b1a80;
  --text:#4a4a4a;
  --peach:#fcd6c3;
  --peach-soft:#fde9de;
  --lavender:#ece6f1;
  --white:#fff;
  --green:#9cc57c;
  --green-light:#dbead0;
}
*{margin:0;padding:0;box-sizing:border-box}
html,body{width:1200px;height:2302px;overflow:hidden}
body{position:relative;background:var(--white);font-family:'Poppins',sans-serif;color:var(--text)}
.abs{position:absolute}

/* header */
.site-header{left:0;top:0;width:1200px;height:95px;background:var(--white)}
.brand{display:flex;align-items:center;gap:10px;font:600 22px 'Poppins',sans-serif;color:var(--purple)}
.header-brand{left:97px;top:26px}
.brand-dot{width:18px;height:18px;border-radius:50%;background:var(--purple)}
.topline{top:22px;font-size:14px;color:#333;white-space:nowrap}
.social-icon{width:14px;height:14px;border-radius:50%;border:2px solid var(--purple);display:block}
.main-nav{left:403px;top:58px;display:flex;gap:24px;font-size:13.5px;color:#333;white-space:nowrap}
.main-nav a{color:inherit;text-decoration:none;padding-bottom:6px}
.main-nav a.active{font-weight:600;border-bottom:2px solid var(--purple)}

/* hero */
.hero{left:0;top:95px;width:1200px;height:545px;
  background:
    radial-gradient(circle at 1020px 250px,rgba(238,214,200,.95) 0,rgba(243,228,220,.7) 160px,rgba(255,255,255,0) 330px),
    radial-gradient(circle at 230px 90px,rgba(255,255,255,.55) 0,rgba(255,255,255,0) 110px),
    radial-gradient(circle at 420px 420px,rgba(255,255,255,.45) 0,rgba(255,255,255,0) 120px),
    radial-gradient(circle at 90px 330px,rgba(255,255,255,.35) 0,rgba(255,255,255,0) 90px),
    linear-gradient(90deg,var(--green) 0%,#b4d49a 25%,var(--green-light) 45%,#f1f1ee 62%,#f7f5f3 100%)}
.hero-curve{left:0;top:540px;width:1200px;height:101px}
.hero-title{left:97px;top:238px;font:700 44px 'Poppins',sans-serif;color:var(--purple);white-space:nowrap}
.hero-sub{left:97px;top:314px;width:480px;font:600 21px/33px 'Poppins',sans-serif;color:#555}
.btn{left:97px;top:419px;width:125px;height:45px;border-radius:23px;background:var(--purple);color:var(--white);font:700 15px 'Open Sans',sans-serif;display:flex;align-items:center;justify-content:center}
.dots{left:573px;top:595px;display:flex;gap:3px}
.dots span{width:10px;height:10px;border-radius:50%;border:1.5px solid var(--white)}
.dots span.on{background:var(--white)}

/* welcome */
.welcome-title{left:0;top:722px;width:1200px;text-align:center;font:600 33px 'Poppins',sans-serif;color:#444}
.welcome-text{left:205px;top:780px;width:790px;text-align:center;font:400 12.5px/25px 'Open Sans',sans-serif;color:#555}
.service{width:240px;text-align:center}
.service-photo{width:238px;height:238px;border-radius:50%;margin:0 auto}
.service h3{margin-top:22px;font:600 21px 'Poppins',sans-serif;color:#444}

/* contact */
.contact{left:0;top:1303px;width:1200px;height:700px;
  background:
    radial-gradient(ellipse 240px 200px at 380px 110px,rgba(246,200,180,.6),rgba(246,200,180,0)),
    linear-gradient(180deg,var(--peach) 0%,#fbd2c0 55%,#f5d3d2 100%)}
.contact-title{left:97px;top:1395px;font:600 29px 'Poppins',sans-serif;color:#3a3a3a}
.contact-intro{left:101px;top:1440px;width:360px;font:400 12.5px/24px 'Open Sans',sans-serif;color:#555}
.info-card{left:97px;top:1502px;width:390px;height:345px;background:var(--peach-soft);box-shadow:0 2px 6px rgba(0,0,0,.08);padding:22px 27px}
.info-card h4{font:600 17px 'Poppins',sans-serif;color:#333;margin-bottom:6px}
.info-card p{font:400 13.5px/26px 'Poppins',sans-serif;color:#444;padding-left:26px}
.info-card .gap{margin-top:18px}
.info-row{display:flex;gap:14px;margin-top:14px;font:400 13.5px/23px 'Poppins',sans-serif;color:#444;padding-left:2px}
.info-row svg{flex:none;margin-top:5px}
.map{left:525px;top:1413px;width:574px;height:430px;
  background:
    linear-gradient(160deg,rgba(255,255,255,0) 40%,rgba(226,228,230,.9) 48%,rgba(255,255,255,0) 56%),
    linear-gradient(180deg,#f8ebe0 0%,#f5e6da 55%,#e9e9e9 100%);
  box-shadow:0 1px 4px rgba(0,0,0,.08)}

/* footer */
.footer{left:0;top:1960px;width:1200px;height:342px;
  background:
    radial-gradient(ellipse 330px 70px at 760px 230px,rgba(205,195,215,.7),rgba(205,195,215,0)),
    linear-gradient(180deg,#f2ecf4 0%,var(--lavender) 60%,#e3dbe8 100%)}
.footer-curve{left:0;top:1935px;width:1200px;height:62px}
.footer-brand{left:97px;top:2120px}
.footer-col h5{font:600 15px 'Poppins',sans-serif;color:#222;margin-bottom:12px}
.footer-col li{list-style:none;font:400 12.5px/22px 'Poppins',sans-serif;color:#444}
.footer-social{display:flex;gap:20px}
.email-field{left:809px;top:2093px;width:292px;height:34px;border:1px solid #555;border-radius:17px;display:flex;align-items:center;justify-content:space-between;padding:0 18px 0 22px;font:400 12.5px 'Poppins',sans-serif;color:#444}
.subscribe{left:810px;top:2144px;width:97px;height:34px;border:1.5px solid var(--purple);border-radius:17px;display:flex;align-items:center;justify-content:center;font:600 12.5px 'Poppins',sans-serif;color:#333}
.copyright{left:97px;top:2268px;font:400 12px 'Poppins',sans-serif;color:#444}
.legal{left:869px;top:2268px;font:400 12px 'Poppins',sans-serif;color:#444;display:flex;gap:12px}
</style>
</head>
<body>

<header class="site-header abs">
  <div class="brand header-brand abs"><span class="brand-dot"></span>Lumera Beauty</div>
  <span class="topline abs" style="left:646px">Tel:23418865</span>
  <span class="topline abs" style="left:763px">Whatsapp:61927430</span>
  <span class="topline abs" style="left:936px">Lan : &nbsp;Eng &#8964;</span>
  <span class="social-icon abs" style="left:1051px;top:24px"></span>
  <span class="social-icon abs" style="left:1085px;top:24px"></span>
  <nav class="main-nav abs">
    <a class="active">Home</a><a>About us</a><a>Promotions &amp; Latest deals</a><a>Treatment &#8964;</a><a>Products Showcase</a><a>Contact us</a>
  </nav>
</header>

<section>
  <div class="hero abs" role="img" aria-label="Banner photo: smiling woman touching her cheek against a soft green bokeh background"></div>
  <svg class="hero-curve abs" viewBox="0 0 1200 101" preserveAspectRatio="none"><path d="M0 20 Q600 160 1200 62 L1200 101 L0 101 Z" fill="#fff"/></svg>
  <h1 class="hero-title abs">Excellent medical beauty</h1>
  <p class="hero-sub abs">Lorem Ipsum is simply dummy text of the printing and typesetting industry.</p>
  <div class="btn abs">Read More</div>
  <div class="dots abs"><span class="on"></span><span></span><span></span><span></span></div>
</section>

<section>
  <h2 class="welcome-title abs">Welcome</h2>
  <p class="welcome-text abs">Lorem Ipsum. Proin gravida nibh vel velit auctor aliquet. Aenean sollicitudin, ipsum, nec sagittise sem nibh id elit. Duis sed odio sit amet nibh vulputate cursus auctor a ornare odio. sed odio sitae &nbsp;amet nibh vulputate cursus a sit amet mauris. Morbi accumsan ipsum velit. Sed non mauris vitae erat.</p>
  <div class="service abs" style="left:169px;top:911px">
    <div class="service-photo" role="img" aria-label="Photo of a facial treatment being applied with a brush" style="background:linear-gradient(160deg,#eeeae6 0%,#e6d8cc 35%,#c89a78 62%,#8a5a3c 85%,#5c3a28 100%)"></div>
    <h3>Facials</h3>
  </div>
  <div class="service abs" style="left:480px;top:911px">
    <div class="service-photo" role="img" aria-label="Photo of hot stones placed on a back" style="background:linear-gradient(180deg,#d98a5e 0%,#b8542e 30%,#3a130a 62%,#050202 100%)"></div>
    <h3>Body Care</h3>
  </div>
  <div class="service abs" style="left:790px;top:911px">
    <div class="service-photo" role="img" aria-label="Photo of a slimming device treatment on the body" style="background:linear-gradient(200deg,#eef1f5 0%,#dfe5ec 40%,#f1d3bc 65%,#e8b896 100%)"></div>
    <h3>Thin Shape</h3>
  </div>
</section>

<section>
  <div class="contact abs" role="img" aria-label="Faint background photo of a relaxed woman receiving a treatment"></div>
  <h2 class="contact-title abs">Contact Us</h2>
  <p class="contact-intro abs">To arrange appointment, please contact us at your convenience. &nbsp;We look forward to meeting you soon.</p>
  <div class="info-card abs">
    <h4>Timing</h4>
    <p>Monday to Friday: 10:30 am to 9:30 pm<br>Saturday and holidays: 10:30 am to 7:30 pm</p>
    <h4 class="gap">Inquiry Hotline</h4>
    <p>23418865<br>61927430</p>
    <div class="info-row">
      <svg width="10" height="14" viewBox="0 0 10 14"><path d="M5 0C2.2 0 0 2.2 0 5c0 3.5 5 9 5 9s5-5.5 5-9C10 2.2 7.8 0 5 0zm0 7a2 2 0 110-4 2 2 0 010 4z" fill="#6b1a80"/></svg>
      <span>12th Floor, Silver Harbour Centre,<br>52-54 Lotus Road<br>Tsim Sha Tsui, Kowloon</span>
    </div>
    <div class="info-row">
      <svg width="12" height="12" viewBox="0 0 12 12"><circle cx="6" cy="6" r="6" fill="#6b1a80"/></svg>
      <span>hello@lumerabeauty.com.hk</span>
    </div>
  </div>
  <div class="map abs" role="img" aria-label="Street map showing the salon location in Tsim Sha Tsui"></div>
</section>

<footer>
  <div class="footer abs" role="img" aria-label="Soft lavender water ripple background"></div>
  <svg class="footer-curve abs" viewBox="0 0 1200 62" preserveAspectRatio="none"><path d="M0 62 Q600 -28 1200 62 L1200 0 L0 0 Z" fill="#f5d3d2"/></svg>
  <div class="brand footer-brand abs"><span class="brand-dot"></span>Lumera Beauty</div>
  <div class="footer-col abs" style="left:351px;top:2045px">
    <h5>Quick Links</h5>
    <ul><li>Home</li><li>About us</li><li>Promotions &amp; Latest deals</li><li>Treatment</li><li>Products Showcase</li><li>Contact us</li></ul>
  </div>
  <div class="footer-col abs" style="left:601px;top:2045px">
    <h5>Follow Us On</h5>
    <div class="footer-social"><span class="social-icon"></span><span class="social-icon"></span></div>
  </div>
  <div class="footer-col abs" style="left:807px;top:2046px"><h5>Join Our Company</h5></div>
  <div class="email-field abs">
    <span>Your Email Address</span>
    <svg width="16" height="12" viewBox="0 0 16 12"><rect x="0.75" y="0.75" width="14.5" height="10.5" rx="1" fill="none" stroke="#6b1a80" stroke-width="1.5"/><path d="M1 1l7 6 7-6" fill="none" stroke="#6b1a80" stroke-width="1.5"/></svg>
  </div>
  <div class="subscribe abs">Subscribe</div>
  <p class="copyright abs">Copyright © 2018 Lumera Beauty. All Rights Reserved.</p>
  <p class="legal abs"><span>Privacy Policy</span><span>|</span><span>Terms &amp; Conditions</span></p>
</footer>

</body>
</html>
```